TINPAILFOLK.COM NEEDS FACELIFT!!!

Please see www.tinpailfolk.com for the basics. I am a glass artist who sells to retail market (art shows and e-commerce) as well as wholsale to art galleries nation wide. My site needs to serve both types of customer. I did the basics years ago, but now it's old and outdated . I need to totally rework the site, adding functionality as well as a new look.
My criteria are:
1. Need e-commerce page (cart) that allows for the rapid uploading of new artwork for my retail market.
2. Need separate login/e-commerce page for my wholesale customers as well as different pricing.
3. Need zip code lookup to show locations of current galleries.
4. Need registration page to collect customer emails/addresses for net marketing (brisk bulletin).
5. Design should be neutral background since I want to highlight to vivid colors of my work.
6. Site should be easy to navigate.
7. I need to have control of adding content to site as needed (new photos, events, etc.)
8. Need page to list upcoming schedule and event dates.
9. Need all the pages and content from old site, with some revisions to be determined after general design is complete.
...Any suggestions on how to make my site more interesting and functional are welcomed!!
Updates
Added photos of newer work today, some of these should appear in high impact areas of the site,. DEan
Question to all...I just remembered that I have already search engine optimized my site using all the appropriate meta tags and photo names, text, etc. for the search terms "glass boxes" and "mosaic mirrors." I am number 1 in zoppo search results of these terms. I need this to not change. Will redesigning my site affect this?
Reason: Hello all, I am in Rome italy right now on business and I have not had time to work with any of you on the designs yet. I am extending the deadline so I can provide more interaction . Dean
Reason: I am still traveling abroad and have no time to work with and review designs. I will be home on the 26th of Oct. then I will be more in touch. Dean
Target Market(s)
mid to high income women
Industry/Entity Type
E-Commerce
Requirements
Must have
- Separate shopping carts for retail and wholesale customers. Wholesale section requires login page.
Lots of pictures of my work. (will supply)
ZIP locator
Broken box repairs page. Customer describes broken piece and can buy replacement part. (size, color, knob color. Can provide pics of all the choices.)
Customer registration page to collect address and email for brisk bulletin or direct mailing.
I like a black or dark gray background of some sort, unless you have a better idea to make my work stand out
Nice to have
- Some kind of link in to social media sites would be great!!!
Should not have
- keep the layout very simple and easy to navigate. Don't want a confusing page

```html
<!DOCTYPE html>
<html lang="en">
<head>
<meta charset="utf-8">
<title>Tin Pail Folk</title>
<link href="https://fonts.googleapis.com/css2?family=Arimo:wght@400;700&family=Ubuntu:wght@700&display=swap" rel="stylesheet">
<style>
:root{
  --ink:#222;
  --muted:#777;
  --header:#1b1b1b;
  --nav:#262626;
  --hero:#141414;
  --band:#3c3c3c;
  --welcome:#e4e4e4;
  --page:#f3f3f3;
  --foot-nav:#2b2b2b;
  --foot:#1d1d1d;
  --white:#fff;
  --field:#5a5a5a;
  --accent-red:#a3161a;
  --accent-blue:#5aa7e0;
}
*{box-sizing:border-box;margin:0;padding:0}
html,body{width:710px;height:1200px;overflow:hidden;background:var(--page)}
body{font-family:"Arimo",Arial,sans-serif;color:var(--ink)}
.canvas{position:relative;width:710px;height:1200px;overflow:hidden;background:var(--page)}
.abs{position:absolute}
.ph{position:absolute}

/* header */
.site-header{left:0;top:0;width:710px;height:55px;background:linear-gradient(#2e2e2e,var(--header))}
.brand{left:36px;top:16px;font-family:"Ubuntu",sans-serif;font-weight:700;font-size:22px;color:#e8e8e8}
.account-links{right:12px;top:23px;font-size:9px;color:#ddd;word-spacing:2px}
.account-links span{margin:0 8px;color:#888}

/* nav */
.main-nav{left:0;top:55px;width:710px;height:33px;background:var(--nav);border-top:1px solid #3a3a3a;border-bottom:1px solid #111}
.main-nav ul{list-style:none;display:flex;height:100%;padding-left:21px}
.main-nav li{font-size:10px;color:#e5e5e5;line-height:31px;padding:0 10px}
.main-nav li.active{background:linear-gradient(#7a7a7a,#4e4e4e);border:1px solid #999;padding:0 15px}

/* hero */
.hero{left:0;top:88px;width:710px;height:262px;background:radial-gradient(ellipse at 50% 40%,#303030,var(--hero) 70%)}
.slide{left:66px;top:104px;width:563px;height:211px;background:linear-gradient(90deg,#fff 55%,#ececec);border:2px solid #cfcfcf}
.slide h1{position:absolute;left:83px;top:48px;font-weight:400;font-size:19px;color:#444}
.slide p{position:absolute;left:83px;top:94px;width:230px;font-size:9px;line-height:17px;color:#555}
.slide-art{left:330px;top:44px;width:125px;height:140px;background:linear-gradient(135deg,#d9d9d9,#6d6d6d 60%,#bdbdbd);border-radius:6px}
.arrow{width:36px;height:36px;background:#bcbcbc;top:191px}
.arrow svg{display:block;margin:10px auto}

/* band */
.tagline-band{left:0;top:350px;width:710px;height:60px;background:linear-gradient(#474747,var(--band))}
.tagline-band p{position:absolute;left:71px;top:22px;font-size:13px;color:#eee}
.btn-more{left:554px;top:370px;width:63px;height:21px;background:linear-gradient(#e8e8e8,#b5b5b5);font-size:10px;line-height:21px;text-align:center;color:#111}

/* welcome */
.welcome{left:0;top:410px;width:710px;height:150px;background:var(--welcome)}
.welcome-text{left:12px;top:424px;width:425px;font-size:8.5px;line-height:14px;color:#444}
.welcome-text strong{font-weight:400;font-size:17px;color:#333;margin-right:3px}
.promo{width:178px;height:64px;background:#111;top:481px}
.promo .ph{left:8px;top:6px;width:38px;height:52px}
.promo p{position:absolute;left:68px;top:10px;font-size:9px;line-height:14px;color:#fff}
.promo .price{color:var(--accent-blue)}
.promo .cta{position:absolute;left:68px;top:42px;width:94px;height:14px;background:linear-gradient(#f2f2f2,#c2c2c2);font-size:7.5px;line-height:14px;text-align:center;color:#222;border-radius:2px}
.registration{left:462px;top:425px;width:201px;height:115px;background:linear-gradient(100deg,#6e6e6e,#e0e0e0 45%,#8a8a8a);box-shadow:0 10px 12px -6px rgba(0,0,0,.35)}
.registration h2{position:absolute;left:0;width:100%;top:8px;text-align:center;font-weight:400;font-size:10.5px;color:#222}
.field{left:41px;width:116px;height:18px;background:var(--field);border:1px solid #888;font-size:7.5px;line-height:16px;color:#ddd;padding-left:10px}
.go{left:643px;top:516px;width:28px;height:28px;border-radius:50%;background:radial-gradient(circle at 40% 35%,#666,#222);font-size:8px;line-height:28px;text-align:center;color:#fff}

/* products */
.section-title{font-weight:400;font-size:13px;color:#222}
.product{width:140px}
.product .ph{left:0;top:0;width:140px;height:82px;border:3px solid #ddd;box-shadow:0 3px 4px rgba(0,0,0,.25)}
.tag{position:absolute;left:134px;top:6px;width:20px;height:24px;background:#3a3a3a;transform:rotate(-40deg);font-size:6px;color:#fff;line-height:24px;text-align:center}
.product h3{position:absolute;left:0;top:95px;font-weight:400;font-size:8.5px;color:#333}
.product p{position:absolute;left:0;top:108px;width:150px;font-size:7.5px;line-height:11px;color:#888}
.product .more{position:absolute;right:0;top:136px;font-size:8px;font-weight:700;color:#222}

/* sidebar */
.event{left:555px;width:144px;height:36px;border-bottom:1px solid #cfcfcf}
.event svg{position:absolute;left:0;top:3px}
.event p{position:absolute;left:29px;top:5px;font-size:6.5px;line-height:13px;color:#888}
.side-box{left:555px;width:144px;height:70px;background:#d5d5d5;border-radius:3px}
.side-box h2{position:absolute;left:6px;top:5px;font-weight:400;font-size:12px;color:#222}
.side-box .rule{position:absolute;left:6px;right:6px;top:22px;border-top:1px solid #aaa}
.side-box .input{position:absolute;left:6px;top:30px;width:121px;height:15px;background:#555;border-radius:3px;font-size:6.5px;line-height:15px;color:#ddd;padding-left:8px}
.side-box .btn{position:absolute;right:6px;bottom:6px;height:13px;padding:0 5px;background:#222;font-size:7px;line-height:13px;color:#fff;border-radius:2px}
.store-title{left:563px;top:967px;font-size:16px;color:var(--accent-red)}
.store-art{left:600px;top:988px;width:92px;height:58px;background:linear-gradient(#c42a2a,#7d1010 70%,#eee 70%)}

/* footer */
.footer-nav{left:0;top:1122px;width:710px;height:36px;background:var(--foot-nav)}
.footer-nav p{position:absolute;left:18px;top:14px;font-size:7.5px;color:#ddd;word-spacing:1px}
.footer-nav span{color:#777;margin:0 5px}
.footer-base{left:0;top:1158px;width:710px;height:42px;background:var(--foot)}
.copyright{left:22px;top:1173px;font-size:7.5px;color:#ccc}
.connect{left:505px;top:1173px;font-size:7.5px;color:#ccc}
.social{top:1167px;width:18px;height:18px;border-radius:50%;background:#8a8a8a}
</style>
</head>
<body>
<div class="canvas">

  <header class="abs site-header">
    <div class="abs brand">Tin Pail Folk</div>
    <div class="abs account-links">My Cart<span>|</span>My Wish List<span>|</span>My Account</div>
  </header>

  <nav class="abs main-nav">
    <ul>
      <li class="active">Home</li><li>About the Artist</li><li>Glass Boxes</li><li>Mosaic Mirrors</li><li>Mosaic Tables</li><li>Store Locator</li><li>Shop Online</li><li>ContactCopycats!</li>
    </ul>
  </nav>

  <section class="abs hero"></section>
  <div class="abs slide">
    <h1>Lorem Ipsum Contantry....</h1>
    <p>Cicero are also reproduced in their exact original form, accompanied by English versions from the 1914 translation by H. Penwright.</p>
    <div class="ph slide-art" role="img" aria-label="Glass cube sculpture"></div>
  </div>
  <div class="abs arrow" style="left:85px"><svg width="10" height="16" viewBox="0 0 10 16"><path d="M8 1 2 8l6 7" stroke="#fff" stroke-width="2.5" fill="none"/></svg></div>
  <div class="abs arrow" style="left:572px"><svg width="10" height="16" viewBox="0 0 10 16"><path d="M2 1l6 7-6 7" stroke="#fff" stroke-width="2.5" fill="none"/></svg></div>

  <section class="abs tagline-band"><p>Unique Glass Boxes and Mosaic Mirrors by Dean Harrow and Ruth Calder</p></section>
  <div class="abs btn-more">View More</div>

  <section class="abs welcome"></section>
  <p class="abs welcome-text"><strong>Welcome to Dean Harrow studio</strong> Home of TinPailFolk. This site features the creative works of Michigan artists Dean Harrow and Ruth Calder. Please browse through. We hope you enjoy our fun, whimsical and even elegant glass boxes, mirrors and contemporary sculpture.</p>

  <div class="abs promo" style="left:20px">
    <div class="ph" role="img" aria-label="Colourful glass gift box" style="background:linear-gradient(#444,#a33 50%,#2a6)"></div>
    <p>Great, Unique Gift Ideas!<br><span class="price" style="margin-left:60px">from $25!</span></p>
    <div class="cta">Click for Glass Boxes</div>
  </div>
  <div class="abs promo" style="left:213px">
    <div class="ph" role="img" aria-label="Mosaic mirror" style="background:linear-gradient(135deg,#7a3b1c,#c9803a,#3a2410)"></div>
    <p>Perfect for Bathroom,<br>Hall or Foyer <span class="price">$100-$1500</span></p>
    <div class="cta">Click for Mosaic Mirrors</div>
  </div>

  <div class="abs registration">
    <h2>Registration</h2>
    <div class="abs field" style="top:30px">E-mail ID</div>
    <div class="abs field" style="top:53px">Username</div>
    <div class="abs field" style="top:77px">Password</div>
  </div>
  <div class="abs go">Go</div>

  <h2 class="abs section-title" style="left:12px;top:571px">Products</h2>
  <h2 class="abs section-title" style="left:555px;top:571px">Upcoming Events</h2>

  <!-- product grid -->
  <div class="abs product" style="left:12px;top:602px"><div class="ph" role="img" aria-label="Patterned glass chest of drawers" style="background:linear-gradient(135deg,#2f4a8a,#b23a3a,#7bb04a)"></div><span class="tag">Buy</span><h3>Lorem Ipsum</h3><p>Cicero are also reproduced in their exact original form, accompanied.</p><span class="more">View more</span></div>
  <div class="abs product" style="left:190px;top:602px"><div class="ph" role="img" aria-label="Three whimsical glass boxes on legs" style="background:linear-gradient(90deg,#e23b3b,#7a59a8,#5fb0c8)"></div><span class="tag">Buy</span><h3>Lorem Ipsum</h3><p>Cicero are also reproduced in their exact original form, accompanied.</p><span class="more">View more</span></div>
  <div class="abs product" style="left:368px;top:602px"><div class="ph" role="img" aria-label="Small mosaic mirror on a wall" style="background:radial-gradient(#c87a8a,#c49a5e 60%)"></div><span class="tag">Buy</span><h3>Lorem Ipsum</h3><p>Cicero are also reproduced in their exact original form, accompanied.</p><span class="more">View more</span></div>

  <div class="abs product" style="left:12px;top:780px"><div class="ph" role="img" aria-label="Round mosaic mirror on brick wall" style="background:radial-gradient(#c9c9c9 25%,#2a2a2a 40%,#9a5a3c 60%)"></div><span class="tag">Buy</span><h3>Lorem Ipsum</h3><p>Cicero are also reproduced in their exact original form, accompanied.</p><span class="more">View more</span></div>
  <div class="abs product" style="left:190px;top:780px"><div class="ph" role="img" aria-label="Wall display of mosaic pieces" style="background:linear-gradient(135deg,#c7a12a,#b8302a,#6a4a1a)"></div><span class="tag">Buy</span><h3>Lorem Ipsum</h3><p>Cicero are also reproduced in their exact original form, accompanied.</p><span class="more">View more</span></div>
  <div class="abs product" style="left:368px;top:780px"><div class="ph" role="img" aria-label="Blue patterned glass box" style="background:linear-gradient(135deg,#9a8b6a,#3d4f8a,#6a7a5a)"></div><span class="tag">Buy</span><h3>Lorem Ipsum</h3><p>Cicero are also reproduced in their exact original form, accompanied.</p><span class="more">View more</span></div>

  <div class="abs product" style="left:12px;top:958px"><div class="ph" role="img" aria-label="Leopard pattern glass box" style="background:linear-gradient(#c9b28a,#6a4a22 60%,#a88a5a)"></div><span class="tag">Buy</span><h3>Lorem Ipsum</h3><p>Cicero are also reproduced in their exact original form, accompanied.</p><span class="more">View more</span></div>
  <div class="abs product" style="left:190px;top:958px"><div class="ph" role="img" aria-label="Black and gold glass box" style="background:linear-gradient(#222,#6a5a2a 60%,#1a1a1a)"></div><span class="tag">Buy</span><h3>Lorem Ipsum</h3><p>Cicero are also reproduced in their exact original form, accompanied.</p><span class="more">View more</span></div>
  <div class="abs product" style="left:368px;top:958px"><div class="ph" role="img" aria-label="Room with grid patterned glass pieces" style="background:linear-gradient(135deg,#ddd,#8a8a8a,#c23a3a)"></div><span class="tag">Buy</span><h3>Lorem Ipsum</h3><p>Cicero are also reproduced in their exact original form, accompanied.</p><span class="more">View more</span></div>

  <!-- events -->
  <div class="abs event" style="top:596px"><svg width="23" height="24" viewBox="0 0 23 24"><rect x="1" y="3" width="21" height="20" fill="none" stroke="#aaa"/><rect x="1" y="3" width="21" height="5" fill="#ccc"/><text x="11.5" y="20" font-size="10" fill="#999" text-anchor="middle" font-family="Arimo,sans-serif">27</text></svg><p>Lorem Ipsum Contantry to Popular<br>Belive dummy text in English</p></div>
  <div class="abs event" style="top:632px"><svg width="23" height="24" viewBox="0 0 23 24"><rect x="1" y="3" width="21" height="20" fill="none" stroke="#aaa"/><rect x="1" y="3" width="21" height="5" fill="#ccc"/><text x="11.5" y="20" font-size="10" fill="#999" text-anchor="middle" font-family="Arimo,sans-serif">27</text></svg><p>Lorem Ipsum Contantry to Popular<br>Belive dummy text in English</p></div>
  <div class="abs event" style="top:668px"><svg width="23" height="24" viewBox="0 0 23 24"><rect x="1" y="3" width="21" height="20" fill="none" stroke="#aaa"/><rect x="1" y="3" width="21" height="5" fill="#ccc"/><text x="11.5" y="20" font-size="10" fill="#999" text-anchor="middle" font-family="Arimo,sans-serif">27</text></svg><p>Lorem Ipsum Contantry to Popular<br>Belive dummy text in English</p></div>
  <div class="abs event" style="top:704px"><svg width="23" height="24" viewBox="0 0 23 24"><rect x="1" y="3" width="21" height="20" fill="none" stroke="#aaa"/><rect x="1" y="3" width="21" height="5" fill="#ccc"/><text x="11.5" y="20" font-size="10" fill="#999" text-anchor="middle" font-family="Arimo,sans-serif">27</text></svg><p>Lorem Ipsum Contantry to Popular<br>Belive dummy text in English</p></div>
  <div class="abs event" style="top:740px"><svg width="23" height="24" viewBox="0 0 23 24"><rect x="1" y="3" width="21" height="20" fill="none" stroke="#aaa"/><rect x="1" y="3" width="21" height="5" fill="#ccc"/><text x="11.5" y="20" font-size="10" fill="#999" text-anchor="middle" font-family="Arimo,sans-serif">27</text></svg><p>Lorem Ipsum Contantry to Popular<br>Belive dummy text in English</p></div>

  <div class="abs side-box" style="top:794px"><h2>News Letter</h2><div class="rule"></div><div class="input">Enter your Mail ID</div><div class="btn">Subscribe</div></div>
  <div class="abs side-box" style="top:880px"><h2>Store Locator</h2><div class="rule"></div><div class="input">Enter your ZIP Code</div><div class="btn">Find Dealers</div></div>

  <div class="abs store-title">Online Store</div>
  <div class="ph store-art" role="img" aria-label="Red BUY lettering with computer mouse"></div>

  <footer class="abs footer-nav"><p>Home<span>|</span>About the Artist<span>|</span>Glass Boxes<span>|</span>Mosaic Mirrors<span>|</span>Mosaic Tables<span>|</span>Other Photos<span>|</span>Store Locator<span>|</span>Shop Online<span>|</span>Show Schedule<span>|</span>Wholesale<span>|</span>Contact<span>|</span>Copycats!</p></footer>
  <div class="abs footer-base"></div>
  <div class="abs copyright">Copyright © 2011 www.tinpailfolk.com All rights reserved</div>
  <div class="abs connect">Connect with us:</div>
  <div class="abs social" style="left:569px" role="img" aria-label="Social network link"></div>
  <div class="abs social" style="left:594px" role="img" aria-label="Social network link"></div>
  <div class="abs social" style="left:619px" role="img" aria-label="Social network link"></div>
  <div class="abs social" style="left:644px" role="img" aria-label="Feed link"></div>
  <div class="abs social" style="left:669px" role="img" aria-label="Video network link"></div>

</div>
</body>
</html>
```